Coastal Learner Bureau business cards

Australian company about to start offering its services. We recruit international students to come to study English, vocational education and postgraduate courses in Australia. We help them find the institution and select the right city they want to come to Australia. We are a young, online oriented and supportive agency. Our clients are between 18 and 35 years old, mainly University students, young professionals or people with work experience. We provide much more information that any other agency offer. We administrate a Facebook group with more than 11.000 members that daily ask questions about general information when coming to Australia, while they are here and even after they leave the country

Target Market(s)

International students from South America, Central America and Europe

Industry/Entity Type

Student

Contact Information for Business Card

Tomas Bilbrea
Managing Director
tomas@kelvarin.com.au
www.kelvoria.com.au
+61 491058264
Melbourne, Australia

Font styles to use
Serif
Sans Serif

Colors

Designer to choose colors to be used in the design.

Requirements
Must have
• Horizontal design
• Standard business card size and shape. If font uses green or yellow colours, they will have to match the ones from the logo
Nice to have
• UPDATE: Use the contents of the green image to design one of the card sides. Use our logo in the background of that side as watermark.
• Passport image, or immigration stamps. A picture of the Yarra River (from Melbourne) would be cool as well.
Should not have
• Non-standard business card size and shape
• Not black as the background colour of any sides as we are not a VIP agency or a hight class service. We are orientes to young people and they like colours, pictures, something attractive.
• Vertical design
• NO YELLOW or BLACK AS THE BACKGROUND COLOUR OF ANY SIDE OF THE BIZ CARD

```html
<!DOCTYPE html>
<html lang="en">
<head>
<meta charset="utf-8">
<title>Coastal Learner Bureau business cards</title>
<link rel="stylesheet" href="https://fonts.googleapis.com/css2?family=PT+Sans:ital,wght@0,400;0,700;1,700&display=swap">
<style>
  :root {
    --green-light: #178a5a;
    --green-dark: #0e643f;
    --brand-green: #12603a;
    --yellow: #e6bd12;
    --white: #ffffff;
    --paper: #f3f3f1;
    --backdrop: #e6e2da;
  }
  * { margin: 0; padding: 0; box-sizing: border-box; }
  html, body { width: 1200px; height: 960px; overflow: hidden; }
  body {
    background: var(--backdrop);
    font-family: "PT Sans", Arial, sans-serif;
    position: relative;
  }
  .card {
    position: absolute;
    width: 600px;
    height: 343px;
    border-radius: 22px;
    overflow: hidden;
    box-shadow: 0 3px 8px rgba(0,0,0,0.25);
  }
  .card--front { left: 302px; top: 128px; }
  .card--back {
    left: 298px; top: 488px;
    background: linear-gradient(135deg, var(--green-light), var(--green-dark));
  }
  .card__art { position: absolute; inset: 0; }
  .contact { position: absolute; left: 38px; top: 100px; color: var(--white); }
  .contact__name { color: var(--yellow); font-size: 22px; font-weight: 700; line-height: 1; }
  .contact__role { font-size: 16px; margin-top: 4px; }
  .contact__city { font-size: 14px; margin-top: 12px; }
  .contact__list { list-style: none; margin-top: 10px; font-size: 14px; }
  .contact__list li { display: flex; align-items: center; gap: 9px; height: 19px; }
  .contact__list svg { width: 13px; height: 13px; flex: none; }
  .wordmark { position: absolute; font-weight: 700; line-height: 1; white-space: nowrap; }
  .wordmark--front { left: 318px; width: 282px; top: 150px; text-align: center; font-size: 50px; color: var(--brand-green); }
  .wordmark--back { left: 0; width: 600px; top: 122px; text-align: center; font-size: 84px; color: var(--white); }
  .tagline {
    position: absolute; left: 0; width: 600px; top: 296px;
    display: flex; align-items: center; justify-content: center; gap: 6px;
    color: var(--white); font-size: 15px; font-weight: 700; font-style: italic;
  }
  .tagline__rule { width: 106px; height: 1px; background: rgba(255,255,255,0.8); }
</style>
</head>
<body>
  <section class="card card--front" aria-label="Business card front">
    <svg class="card__art" viewBox="0 0 600 343" aria-hidden="true">
      <defs>
        <linearGradient id="front-green" x1="0" y1="0" x2="1" y2="1">
          <stop offset="0" stop-color="#178a5a"/>
          <stop offset="1" stop-color="#0e643f"/>
        </linearGradient>
      </defs>
      <rect width="600" height="343" fill="url(#front-green)"/>
      <path d="M296,0 Q226,172 300,343 L316,343 Q244,172 306,0 Z" fill="#e6bd12"/>
      <path d="M318,0 Q236,172 318,343 L600,343 L600,0 Z" fill="#f3f3f1"/>
    </svg>
    <div class="contact">
      <p class="contact__name">Tomas Bilbrea</p>
      <p class="contact__role">Managing Director</p>
      <p class="contact__city">Melbourne, Australia</p>
      <ul class="contact__list">
        <li><svg viewBox="0 0 16 16"><path d="M3 1l3 3-1.5 2a9 9 0 0 0 5.5 5.5L12 10l3 3-2 2C7 15 1 9 1 3z" fill="#e6bd12"/></svg>+61 491058264</li>
        <li><svg viewBox="0 0 16 16"><rect x="1" y="3" width="14" height="10" fill="#e6bd12"/><path d="M1 3l7 6 7-6" stroke="#0e643f" stroke-width="1.4" fill="none"/></svg>tomas@kelvarin.com.au</li>
        <li><svg viewBox="0 0 16 16"><circle cx="8" cy="8" r="7" fill="#e6bd12"/><path d="M1 8h14M8 1c-3 4-3 10 0 14M8 1c3 4 3 10 0 14" stroke="#0e643f" stroke-width="1.1" fill="none"/></svg>www.kelvoria.com.au</li>
      </ul>
    </div>
    <p class="wordmark wordmark--front">Kelvoria</p>
  </section>

  <section class="card card--back" aria-label="Business card back">
    <p class="wordmark wordmark--back">Kelvoria</p>
    <p class="tagline"><span class="tagline__rule"></span>Hacemos más por ti!<span class="tagline__rule"></span></p>
  </section>
</body>
</html>
```